Binder design for a veterinary clinic

We are seeking a talented designer to create a standout design for ring binders specifically for our veterinary clinic. These binders will be used to organize materials from our Continuing Professional Development (CPD) projects for colleagues and interns. The design should be clean, professional, and align with our brand guidelines. To give you a better understanding of our branding, we’ve included the design of our vehicles as a reference. As additional reference, please visit www.tierpraxora.at

Target Market(s)

veterinarians

Industry/Entity Type

Veterinary

Font styles to use
Sans Serif

Colors
0054AA
0677BA
7BADD7
CADEEF
E8F1F8
FFC000
F8CF3A
FAE287
FDF2CF
FEFAEE

Requirements
Must have
• Our Logo an a clean design
Should not have
• to much images

```html
<!DOCTYPE html>
<html lang="de">
<head>
<meta charset="utf-8">
<title>Tierpraxora – Binder Cover</title>
<link rel="stylesheet" href="https://fonts.googleapis.com/css2?family=Arimo:wght@400;500&display=swap">
<style>
  :root {
    --backdrop: #e3e3e3;
    --cover-navy: #415366;
    --cover-navy-dark: #34475a;
    --accent-gold: #d8a82c;
    --panel-white: #f1f1ee;
    --icon-white: #ffffff;
  }
  * { margin: 0; padding: 0; box-sizing: border-box; }
  html, body {
    width: 1200px;
    height: 900px;
    overflow: hidden;
    background: var(--backdrop);
  }
  .canvas {
    position: relative;
    width: 1200px;
    height: 900px;
    background: radial-gradient(ellipse at 50% 40%, #ebebeb 0%, var(--backdrop) 70%);
  }
  .binder-cover {
    position: absolute;
    left: 270px;
    top: 130px;
    width: 660px;
    height: 640px;
    overflow: hidden;
    background: linear-gradient(135deg, #4d6074 0%, var(--cover-navy) 50%, var(--cover-navy-dark) 100%);
    box-shadow: 0 18px 40px rgba(0, 0, 0, 0.18);
  }
  .arc-motif {
    position: absolute;
    inset: 0;
  }
  .brand-name {
    position: absolute;
    left: 480px;
    top: 240px;
    width: 180px;
    text-align: center;
    font-family: "Arimo", Arial, sans-serif;
    font-weight: 500;
    font-size: 22px;
    letter-spacing: 0.3px;
    color: var(--cover-navy-dark);
  }
  .contact {
    position: absolute;
    left: 184px;
    top: 300px;
    width: 200px;
    text-align: center;
  }
  .contact-icon {
    display: block;
    width: 30px;
    height: 26px;
    margin: 0 auto 12px;
  }
  .contact-phone {
    font-family: "Arimo", Arial, sans-serif;
    font-weight: 500;
    font-size: 22px;
    letter-spacing: 0.5px;
    color: var(--accent-gold);
  }
</style>
</head>
<body>
  <main class="canvas">
    <section class="binder-cover">
      <svg class="arc-motif" width="660" height="640" viewBox="0 0 660 640" aria-hidden="true">
        <circle cx="720" cy="280" r="300" fill="var(--accent-gold)"/>
        <circle cx="720" cy="280" r="284" fill="var(--panel-white)"/>
      </svg>

      <p class="brand-name">Tierpraxora</p>

      <div class="contact">
        <svg class="contact-icon" viewBox="0 0 30 26" aria-hidden="true">
          <path d="M9 6 a9 9 0 0 1 12 0" fill="none" stroke="var(--icon-white)" stroke-width="2" stroke-linecap="round"/>
          <path d="M11.5 9.5 a5 5 0 0 1 7 0" fill="none" stroke="var(--icon-white)" stroke-width="2" stroke-linecap="round"/>
          <path d="M2 15 c4 -4 22 -4 26 0 l0 4 c0 1 -1 2 -2 2 l-4 0 c-1 0 -2 -1 -2 -2 l0 -2 c-3 -1 -7 -1 -10 0 l0 2 c0 1 -1 2 -2 2 l-4 0 c-1 0 -2 -1 -2 -2 z" fill="var(--icon-white)"/>
          <path d="M9 19 c2 4 10 4 12 0" fill="var(--icon-white)"/>
        </svg>
        <p class="contact-phone">+43(0)1 58210</p>
      </div>
    </section>
  </main>
</body>
</html>
```